Business Cards for new orthopaedic surgery practice

My husband and I are starting our own orthopaedic surgery practice. We are looking for a business card that is uniform, but one will have my name/title and the other will have his. You can just create one design with my name on it for now. But when I choose your design as the winning design I will ask that you add another copy with his name/title.

We are looking for classy, simple, elite all in one. We like dark blues/a little gold/yellow. Something that goes with our logo. We want our logo incorporated. Here is all the info you need:
Business name: RV Bone & Vitality Center
Location: 38517 North Willowmere Ave
Maple Hollow, FL 33987
Phone: 954-218-4063
Fax: 954-582-7341
Email: info@myrvbonecare.example

Names: Lydia Vance, M.D.
Board Certified Hand and Upper Extremity Surgeon

Ebo Dansu, M.D.
Board Certified Hip & Knee Replacement/General Orthopaedic Surgeon

Can decide what you want to put on the back. Maybe a slogan:
Grounded in Care. Centered on You

I am just going to upload our logo. The only thing is if we select you as the winning design, the location, and phone numbers may change. We will need your help to update that once fully solidified.

Industry/Entity Type

Medical

Contact Information for Business Card

Colors
0054AA
0677BA
7BADD7
CADEEF
E8F1F8
0094D4
00A9DD
6FCCEA
C7EBF8
E9F6FB

Requirements
Must have
• class, appeal,
Should not have
• We want to air on the side of masculine if we are looking at masculine vs. feminine feel. But we still want it classy, sophisticated, and something we will love

```html
<!DOCTYPE html>
<html lang="en">
<head>
<meta charset="utf-8">
<title>RV Bone &amp; Vitality Center — Business Card</title>
<link href="https://fonts.googleapis.com/css2?family=Playfair+Display:wght@700&family=Poppins:wght@400;500;600&display=swap" rel="stylesheet">
<style>
  :root {
    --navy: #1b2a4e;
    --gold: #c9a56a;
    --white: #ffffff;
    --ink: #1e1e24;
    --rule: #3a3a44;
    --backdrop: #2a2b2e;
  }
  * { margin: 0; padding: 0; box-sizing: border-box; }
  html, body { width: 1200px; height: 900px; overflow: hidden; }
  body {
    background: var(--backdrop);
    font-family: "Poppins", sans-serif;
    position: relative;
  }
  .card {
    position: absolute;
    left: 250px;
    width: 700px;
    height: 400px;
    border-radius: 26px;
    overflow: hidden;
  }
  /* Front */
  .card--front { top: 36px; background: var(--navy); color: var(--white); }
  .brand-seal {
    position: absolute;
    left: 50%; top: 60px;
    transform: translateX(-50%);
    width: 240px; height: 240px;
  }
  .brand-seal svg { position: absolute; inset: 0; }
  .brand-name {
    position: absolute;
    inset: 0;
    display: flex; align-items: center; justify-content: center;
    text-align: center;
    font-family: "Playfair Display", serif;
    font-weight: 700;
    font-size: 26px;
    line-height: 1.2;
    padding: 0 34px;
  }
  .card--front .brand-name { color: var(--white); }
  .slogan {
    position: absolute;
    left: 0; right: 0; top: 322px;
    text-align: center;
    font-size: 17px;
    letter-spacing: 0.5px;
  }
  /* Back */
  .card--back { top: 464px; background: var(--white); color: var(--ink); }
  .swoosh { position: absolute; inset: 0; }
  .doctors { position: absolute; left: 46px; top: 34px; width: 360px; }
  .doctor + .doctor { margin-top: 10px; }
  .doctor-name {
    font-family: "Playfair Display", serif;
    font-weight: 700;
    color: var(--gold);
    font-size: 25px;
    line-height: 1.05;
  }
  .doctor-title { font-size: 15px; line-height: 1.2; }
  .divider { width: 40px; height: 2px; background: var(--navy); margin: 14px 0 0; }
  .address {
    position: absolute; left: 46px; top: 222px;
    font-size: 15px; line-height: 1.3;
  }
  .contacts {
    position: absolute; left: 46px; top: 270px;
    list-style: none; font-size: 15px; line-height: 1.45;
  }
  .contacts li { display: flex; align-items: center; gap: 10px; }
  .contacts svg { width: 12px; height: 12px; fill: var(--gold); flex: none; }
  .appointment { position: absolute; left: 430px; top: 70px; width: 240px; }
  .appointment h2 {
    font-size: 16px; font-weight: 600; letter-spacing: 0.5px;
    text-align: right; padding-bottom: 8px;
    border-bottom: 1px solid var(--rule);
  }
  .appointment .field { display: flex; align-items: flex-end; gap: 8px; font-size: 15px; margin-top: 18px; }
  .appointment .field .line { flex: 1; border-bottom: 1px solid var(--rule); height: 1px; }
  .back-seal {
    position: absolute; left: 480px; top: 232px;
    width: 150px; height: 150px;
    border-radius: 50%;
    background: var(--white);
  }
  .back-seal svg { position: absolute; inset: 0; }
  .back-seal .brand-name { font-size: 17px; color: var(--navy); padding: 0 24px; }
</style>
</head>
<body>

<section class="card card--front" aria-label="Card front">
  <div class="brand-seal">
    <svg viewBox="0 0 240 240" aria-hidden="true">
      <circle cx="120" cy="120" r="112" fill="none" stroke="var(--gold)" stroke-width="2.5"/>
    </svg>
    <div class="brand-name">RV Bone &amp; Vitality Center</div>
  </div>
  <p class="slogan">Grounded in Care. Centered on You</p>
</section>

<section class="card card--back" aria-label="Card back">
  <svg class="swoosh" viewBox="0 0 700 400" preserveAspectRatio="none" aria-hidden="true">
    <path d="M285 400 C 410 318, 560 290, 700 276 L700 400 Z" fill="var(--gold)"/>
    <path d="M308 400 C 430 330, 575 303, 700 292 L700 400 Z" fill="var(--navy)"/>
  </svg>

  <div class="doctors">
    <div class="doctor">
      <p class="doctor-name">Lydia Vance, M.D.</p>
      <p class="doctor-title">Board Certified Hand and<br>Upper Extremity Surgeon</p>
    </div>
    <div class="doctor">
      <p class="doctor-name">Ebo Dansu, M.D.</p>
      <p class="doctor-title">Board Certified Hip &amp; Knee<br>Replacement/General Orthopaedic<br>Surgeon</p>
    </div>
    <div class="divider"></div>
  </div>

  <p class="address">38517 North Willowmere Ave<br>Maple Hollow, FL 33987</p>

  <ul class="contacts">
    <li><svg viewBox="0 0 12 12"><path d="M1 4c0-2 2-3 5-3s5 1 5 3v1H8V4H4v1H1zM2 6h8l1 5H1z"/></svg>954-218-4063</li>
    <li><svg viewBox="0 0 12 12"><rect x="3" y="0" width="6" height="4"/><rect x="0" y="4" width="12" height="8"/></svg>954-582-7341</li>
    <li><svg viewBox="0 0 12 12"><path d="M0 2h12v1L6 7 0 3zM0 4.5l6 4 6-4V10H0z"/></svg>info@myrvbonecare.example</li>
    <li><svg viewBox="0 0 12 12"><circle cx="6" cy="6" r="6"/></svg>www.rvbonecare.example</li>
  </ul>

  <div class="appointment">
    <h2>NEXT APPOINMENT</h2>
    <div class="field">Date <span class="line"></span></div>
    <div class="field">Time <span class="line"></span></div>
  </div>

  <div class="back-seal">
    <svg viewBox="0 0 150 150" aria-hidden="true">
      <circle cx="75" cy="75" r="66" fill="none" stroke="var(--gold)" stroke-width="2"/>
    </svg>
    <div class="brand-name">RV Bone &amp; Vitality Center</div>
  </div>
</section>

</body>
</html>
```